Development of musical artist Tavro Quill's Website

I need a website designed for a reggae musical artist by the name of Tavro Quill. The site should be representative of a Reggae artist from Jamaica that has a Caribbean appeal but also attractive to global audiences. The website should be responsive for all devices (desktop, laptop, mobile). It should be optimized for SEO purposes. Icons for Photoshare, Friendbook, Chirper, VideoHub should be included. The sections of the website should be as follows: Home, Media, News, Bio, Join, Contact. The 'Join' section should be a form for database collection to the fan club. I would like to easily be able to dump this database in an excel or .csv file at any given time. The 'Media' section should be able to showcase video thumbnails and allow persons to play videos through the site and the videos will be fed from VideoHub. The 'News' section will be for announcements and or new releases where the artist is mentioned. The site should also be built in such a way that analytics can be easily implemented. This website should be the main call to action for this artist moving forward. I would also like the website to have a easy to use CMS platform (Wordpress perhaps). The URL for the website will be tavroquillstar.example. Here are the links for some of the social media pages:
VideoHub - https://www.videohub.example/user/TavroQuill
Photoshare - https://www.photoshare.example/tavroquill/
A good website to refer to from a design perspective is https://marvello.example/

Target Market(s)

Reggae and Pop music fans

Industry/Entity Type

Artists

Coding

Number of Pages Required

5+ page

Font styles to use
Sans Serif

Requirements
Must have
• Great design
Nice to have
• Parallax technology

```html
<!DOCTYPE html>
<html lang="en">
<head>
<meta charset="utf-8">
<title>Tavro Quill — Official Site</title>
<link href="https://fonts.googleapis.com/css2?family=Titillium+Web:wght@400;600;700&family=Open+Sans:wght@400;600&display=swap" rel="stylesheet">
<style>
:root{
  --red:#e0141e;
  --red-deep:#c80f18;
  --ink:#161616;
  --dark:#1c1c1c;
  --hero:#221d1a;
  --white:#ffffff;
  --grey:#6a6a6a;
  --line:#bdbdbd;
  --head:"Titillium Web", sans-serif;
  --body:"Open Sans", sans-serif;
}
*{box-sizing:border-box;margin:0;padding:0}
html,body{width:1200px;height:3455px;overflow:hidden}
body{position:relative;background:var(--white);font-family:var(--body);color:var(--ink)}
.abs{position:absolute}
.shape{position:absolute;left:0;width:1200px;display:block}

/* header / hero */
.hero-bg{top:0;height:720px}
.site-logo{left:143px;top:44px;font-family:var(--head);font-weight:700;font-size:22px;color:var(--white);letter-spacing:1px;display:flex;align-items:center;gap:8px}
.site-logo .dot{width:12px;height:12px;background:var(--red);border-radius:50%}
.main-nav{left:620px;top:46px;display:flex;gap:0;font-family:var(--head);font-size:16px;font-weight:600;color:var(--white)}
.main-nav a{color:inherit;text-decoration:none;position:absolute;white-space:nowrap}
.main-nav a.active{color:var(--red)}
.hero-play{left:576px;top:279px}
.hero-title{left:0;width:1200px;top:336px;text-align:center;font-family:var(--head);font-weight:600;font-size:33px;line-height:37px;color:var(--white);letter-spacing:.5px}
.hero-arrow{top:328px}

/* media */
.section-title{font-family:var(--head);font-weight:600;text-align:center;width:1200px;left:0}
.media-title{top:785px;font-size:42px;color:var(--red)}
.media-nav{top:800px;width:24px;height:24px;border:1.5px solid var(--ink);display:flex;align-items:center;justify-content:center}
.thumb{position:absolute;display:flex;align-items:center;justify-content:center}
.thumb-feature{left:371px;top:857px;width:456px;height:276px;background:linear-gradient(135deg,#5a2512,#a2461c 45%,#3b1a10);box-shadow:0 10px 14px -8px rgba(0,0,0,.35)}

/* news */
.news-bg{top:1225px;height:520px}
.news-title{top:1292px;font-size:40px;color:var(--white)}
.news-card{position:absolute;top:1368px;width:431px;height:150px;background:var(--white);padding:18px 22px}
.news-card time{display:block;font-family:var(--head);font-size:15px;color:var(--red)}
.news-card h3{font-family:var(--head);font-weight:700;font-size:15px;margin-top:14px;letter-spacing:.2px}
.news-card p{font-size:9.5px;line-height:13px;color:var(--grey);margin-top:8px}
.btn-outline{left:548px;top:1557px;width:104px;height:37px;border:1.5px solid var(--white);color:var(--white);font-family:var(--head);font-size:11.5px;display:flex;align-items:center;justify-content:center;border-radius:2px}

/* bio */
.bio-title{left:143px;top:1812px;font-family:var(--head);font-weight:600;font-size:40px;color:var(--red)}
.bio-text{left:143px;top:1888px;width:462px;font-size:14.5px;line-height:26px;color:#2a2a2a}
.bio-text p+p{margin-top:21px}

/* join */
.join-bg{top:2317px;height:390px}
.join-title{top:2382px;font-size:40px;color:var(--white)}
.join-sub{top:2440px;font-size:18px;color:var(--white);font-family:var(--head);text-align:center;width:1200px;left:0}
.field{position:absolute;background:var(--white);border:1.5px solid #b5b5b5;font-size:14px;color:var(--ink);padding:0 16px;display:flex;align-items:center}
.field.top{align-items:flex-start;padding-top:14px}
.btn-solid{position:absolute;background:var(--ink);color:var(--white);font-family:var(--head);font-weight:600;font-size:15px;display:flex;align-items:center;justify-content:center}

/* contact */
.contact-title{top:2773px;font-size:40px;color:var(--red)}
.contact-mail{top:2836px;left:0;width:1200px;display:flex;justify-content:center;align-items:center;gap:10px;font-size:18px;color:#222}

/* footer */
.footer-bg{top:3250px;height:205px}
.footer-links{left:143px;top:3376px;font-size:11.5px;color:#d8d8d8;word-spacing:2px}
.footer-copy{left:143px;top:3406px;font-size:11.5px;color:#d8d8d8}
.social{right:143px;top:3392px;display:flex;gap:16px;font-size:12px;color:#d8d8d8}
.social a{color:inherit;text-decoration:none}
</style>
</head>
<body>

<!-- HERO -->
<svg class="shape hero-bg" viewBox="0 0 1200 720" role="img" aria-label="Dark concert-light photo of the artist in profile">
  <defs>
    <radialGradient id="heroGlow" cx="0.55" cy="0.45" r="0.7">
      <stop offset="0" stop-color="#4a3a2e"/>
      <stop offset="0.6" stop-color="#231c18"/>
      <stop offset="1" stop-color="#0f0d0c"/>
    </radialGradient>
  </defs>
  <polygon points="0,0 1200,0 1200,615 600,706 275,617 0,652" fill="url(#heroGlow)"/>
  <polygon points="275,617 600,706 1200,615 1200,632 600,720 275,626" fill="#e0141e"/>
</svg>

<div class="abs site-logo"><span>TAVRO QUILL</span><span class="dot"></span></div>
<nav class="abs main-nav">
  <a class="active" href="#home" style="left:27px">HOME</a>
  <a href="#media" style="left:108px">MEDIA</a>
  <a href="#news" style="left:186px">NEWS</a>
  <a href="#bio" style="left:244px">BIO</a>
  <a href="#join" style="left:305px">JOIN</a>
  <a href="#contact" style="left:369px">CONTACT</a>
</nav>

<svg class="abs hero-play" width="46" height="46" viewBox="0 0 46 46"><circle cx="23" cy="23" r="22" fill="#fff"/><polygon points="18,13 33,23 18,33" fill="#161616"/></svg>
<h1 class="abs hero-title">VESTIBULUM CONDIMENTUM<br>RISUS POSUERE</h1>
<svg class="abs hero-arrow" style="left:52px" width="20" height="30" viewBox="0 0 20 30"><polyline points="15,4 5,15 15,26" fill="none" stroke="#fff" stroke-width="3"/></svg>
<svg class="abs hero-arrow" style="left:1127px" width="20" height="30" viewBox="0 0 20 30"><polyline points="5,4 15,15 5,26" fill="none" stroke="#fff" stroke-width="3"/></svg>

<!-- MEDIA -->
<h2 class="abs section-title media-title" id="media">MEDIA</h2>
<div class="abs media-nav" style="left:491px"><svg width="10" height="10" viewBox="0 0 10 10"><polyline points="7,1 3,5 7,9" fill="none" stroke="#161616" stroke-width="1.6"/></svg></div>
<div class="abs media-nav" style="left:682px"><svg width="10" height="10" viewBox="0 0 10 10"><polyline points="3,1 7,5 3,9" fill="none" stroke="#161616" stroke-width="1.6"/></svg></div>

<div class="thumb" style="left:0;top:914px;width:138px;height:159px;background:linear-gradient(160deg,#6c7466,#3d4540)" role="img" aria-label="Video thumbnail, outdoor scene"></div>
<div class="thumb" style="left:145px;top:914px;width:219px;height:159px;background:linear-gradient(160deg,#2a2c30,#0e0f12)" role="img" aria-label="Video thumbnail, night scene">
  <svg width="40" height="40" viewBox="0 0 46 46"><circle cx="23" cy="23" r="22" fill="#fff"/><polygon points="18,13 33,23 18,33" fill="#161616"/></svg>
</div>
<div class="thumb thumb-feature" role="img" aria-label="Featured music video poster in rusty orange tones">
  <svg width="44" height="44" viewBox="0 0 46 46"><circle cx="23" cy="23" r="22" fill="#fff"/><polygon points="18,13 33,23 18,33" fill="#161616"/></svg>
</div>
<div class="thumb" style="left:838px;top:914px;width:217px;height:159px;background:linear-gradient(160deg,#7c8590,#4c545c)" role="img" aria-label="Video thumbnail, aerial street view">
  <svg width="40" height="40" viewBox="0 0 46 46"><circle cx="23" cy="23" r="22" fill="#fff"/><polygon points="18,13 33,23 18,33" fill="#161616"/></svg>
</div>
<div class="thumb" style="left:1062px;top:914px;width:138px;height:159px;background:linear-gradient(160deg,#33465e,#8c9aad)" role="img" aria-label="Video thumbnail, blue portrait artwork"></div>

<!-- NEWS -->
<svg class="shape news-bg" viewBox="0 0 1200 520" preserveAspectRatio="none" aria-hidden="true">
  <polygon points="0,0 1200,0 1200,455 925,417 600,515 0,417" fill="#1d1d1d"/>
  <polygon points="0,417 600,515 600,520 0,430" fill="#e0141e"/>
</svg>
<h2 class="abs section-title news-title" id="news">NEWS</h2>
<article class="news-card" style="left:145px">
  <time>17 Januray, 2018</time>
  <h3>PELLENTESQUE A IMPERDIET DOLOR, ET AUCTOR EST.</h3>
  <p>Nulla facilisi. Vestibulum pharetra diam ex, in posuere purus efficitur ac. Mauris placerat eros lorem, vel egestas mi mattis eget. Donec a nisl vel ante tristique mollis nec quis est. Praesent accumsan nunc a condimentum volutpat</p>
</article>
<article class="news-card" style="left:624px">
  <time>17 Januray, 2018</time>
  <h3>PROIN PLACERAT DAPIBUS GRAVIDA</h3>
  <p>Nulla facilisi. Vestibulum pharetra diam ex, in posuere purus efficitur ac. Mauris placerat eros lorem, vel egestas mi mattis eget. Donec a nisl vel ante tristique mollis nec quis est. Praesent accumsan nunc a condimentum volutpat</p>
</article>
<div class="abs btn-outline">READ MORE</div>

<!-- BIO -->
<h2 class="abs bio-title" id="bio">BIO</h2>
<div class="abs bio-text">
  <p>Aliquam erat volutpat. Quisque aliquet ex nec est vestibulum pulvinar. Pellentesque convallis molestie enim sit amet efficitur. Etiam id imperdiet lectus. Vivamus lacus justo, ultrices nec erat in, euismod iaculis mauris. Vivamus eleifend vitae nulla vel malesuada. In ac malesuada lacus, et consectetur ante. Fusce vitae lectus sit amet mi pulvinar maximus.</p>
  <p>Aenean placerat, nibh vel accumsan aliquet, magna nibh accumsan nibh, ac tempus nunc ipsum ac tellus. Cras augue magna, placerat eget nulla non, congue suscipit neque. Sed tellus ex, imperdiet eget gravida sit amet, volutpat eget turpis. In nec ultricies est. Etiam mattis augue vehicula odio posuere, sit amet tempus lectus luctus. Nulla facilisi. Etiam vel massa elementum, bibendum tellus venenatis, feugiat massa. Curabitur venenatis lacinia ornare.</p>
</div>
<svg class="abs" style="left:640px;top:1824px" width="416" height="416" viewBox="0 0 416 416">
  <rect x="78" y="78" width="260" height="260" fill="#e2e2e2" transform="rotate(30 208 208)"/>
  <g role="img" aria-label="Portrait of the artist">
    <defs><radialGradient id="bioShade" cx="0.5" cy="0.45" r="0.6"><stop offset="0" stop-color="#5a3220"/><stop offset="1" stop-color="#1a0f0a"/></radialGradient></defs>
    <rect x="78" y="78" width="260" height="260" fill="url(#bioShade)" transform="rotate(45 208 208)"/>
  </g>
</svg>

<!-- JOIN -->
<svg class="shape join-bg" viewBox="0 0 1200 390" preserveAspectRatio="none" aria-hidden="true">
  <polygon points="0,0 1200,0 1200,285 600,378 0,285" fill="#e0141e"/>
  <polygon points="0,285 600,378 1200,285 1200,295 600,390 0,300" fill="#1d1d1d" opacity="0"/>
  <polygon points="270,327 600,378 1200,285 1200,295 600,390" fill="#1d1d1d"/>
</svg>
<h2 class="abs section-title join-title" id="join">JOIN</h2>
<p class="abs join-sub">Phasellus nisl est, condimentum vitae faucibus in, sollicitudin vel metus</p>
<div class="field" style="left:272px;top:2480px;width:255px;height:47px;border-color:#fff">Name</div>
<div class="field" style="left:543px;top:2480px;width:256px;height:47px;border-color:#fff">Email</div>
<div class="btn-solid" style="left:815px;top:2480px;width:111px;height:47px">SUBSCRIBE</div>

<!-- CONTACT -->
<h2 class="abs section-title contact-title" id="contact">CONTACT US</h2>
<div class="abs contact-mail">
  <svg width="18" height="14" viewBox="0 0 18 14"><rect x="0" y="0" width="18" height="14" rx="1.5" fill="#222"/><polyline points="1,1.5 9,8 17,1.5" fill="none" stroke="#fff" stroke-width="1.5"/></svg>
  <span>info@tavroquillstar.example</span>
</div>
<div class="field" style="left:336px;top:2879px;width:256px;height:48px">Name</div>
<div class="field" style="left:608px;top:2879px;width:256px;height:48px">Email</div>
<div class="field top" style="left:336px;top:2946px;width:528px;height:158px">Message</div>
<div class="btn-solid" style="left:544px;top:3134px;width:110px;height:47px">SUBMIT</div>

<!-- FOOTER -->
<svg class="shape footer-bg" viewBox="0 0 1200 205" preserveAspectRatio="none" aria-hidden="true">
  <polygon points="0,107 600,12 1200,107 1200,205 0,205" fill="#1d1d1d"/>
  <polygon points="0,107 600,0 900,48 600,12" fill="#e0141e"/>
</svg>
<div class="abs footer-links">Home &nbsp;|&nbsp; Media &nbsp;|&nbsp; News &nbsp;|&nbsp; Bio &nbsp;|&nbsp; Join &nbsp;|&nbsp; Contact</div>
<div class="abs footer-copy">Copyright &copy; 2019 Tavro Quill. &nbsp; All rights reserved.</div>
<div class="abs social">
  <a href="#">Friendbook</a>
  <a href="#">Chirper</a>
  <a href="https://www.videohub.example/user/TavroQuill">VideoHub</a>
  <a href="https://www.photoshare.example/tavroquill/">Photoshare</a>
</div>

</body>
</html>
```